Create a Brochure Design for Brantley Homecare

Brantley Homecare is a subsidiary of the Brantley Care Group. This brochure is specifically for the Brantley Homecare company and brand. Create a 3 panel, A4, front and back, tri-fold brochure. This brochure will be a way to introduce our Homecare services to the community, prospective clients, and various referral partners. The brochure must be eye catching, unique in its deliverables and demonstrate both attention to detail and comfort. Our organization is sophisticated and built around warmth, care and individualized personal attention. The most important aspect of this design is to focus on creating a nurturing, warm, and inviting feel where you would want to have a Nurse or Nurse’s Aide in your own home or a loved one’s home.

I am open to the creativity of the designer to develop something based on the above criteria; however I would like the design to work well with the existing collateral material. What I mean by that is that while I want everything to have its own personality and stand out as its own brand representative, I still need to be able to tell that the overall design concept stays stylistically inside of the same ‘family’ of existing designed material. Because of this, below I would like for the designer to pull inspiration from the link to our website (Located below) as well as from the attachment of our recently refreshed business cards (Attached). This should allow each design to be unique and creative, while still staying inside of a framework and the feel/style that I am looking for.

Finally, I want all the designers to understand that this brochure design is for a private, in home, healthcare company where we are responsible for providing personalized care for a culturally and ethnically diverse make-up clientele of all ages. The photos that are used must represent an image of warmth, care, and a positive interaction between client and caregiver.

Look under the Brantley Homecare tab at www.brantleycaregroup.example

Industry/Entity Type

Healthcare

Requirements
Must have
• • The Brantley Homecare company logo must be included.

```html
<!DOCTYPE html>
<html lang="en">
<head>
<meta charset="utf-8">
<title>Brantley Homecare – Tri-fold Inside</title>
<link rel="stylesheet" href="https://fonts.googleapis.com/css2?family=Lora:wght@400;700&display=swap">
<style>
  :root {
    --green: #0e6b5c;
    --green-dark: #0a5a4d;
    --salmon: #f3a288;
    --ink: #4a4a4a;
    --white: #ffffff;
    --photo-warm-1: #d9c3b3;
    --photo-warm-2: #9fb1c4;
    --photo-soft-1: #e8e4dc;
    --photo-soft-2: #a9b69e;
    --photo-rose-1: #e7d4c7;
    --photo-rose-2: #d49a93;
  }
  html, body { margin: 0; padding: 0; overflow: hidden; background: var(--white); }
  .brochure {
    position: relative; width: 1200px; height: 848px; overflow: hidden;
    font-family: "Lora", Georgia, serif; color: var(--ink); background: var(--white);
  }
  .brochure__art { position: absolute; inset: 0; }
  .panel { position: absolute; top: 0; height: 848px; }
  .panel--about { left: 30px; width: 350px; }
  .panel--team { left: 426px; width: 350px; color: var(--white); }
  .panel--services { left: 824px; width: 351px; }
  .section-title {
    position: absolute; top: 366px; margin: 0;
    font-size: 23px; font-weight: 700; color: var(--green); letter-spacing: 0.3px;
  }
  .body-copy {
    margin: 0 0 18px; font-size: 15px; line-height: 19px; text-align: justify;
  }
  .about-copy { position: absolute; top: 417px; width: 350px; }
  .team-block { position: absolute; width: 350px; }
  .team-block--pros { top: 417px; }
  .team-block--nurse { top: 594px; }
  .team-heading { margin: 0 0 22px; font-size: 17px; line-height: 22px; font-weight: 700; }
  .team-block--nurse .team-heading { margin-bottom: 20px; }
  .check-list { list-style: none; margin: 0; padding: 0; font-size: 15px; line-height: 18px; }
  .check-list li { position: relative; padding-left: 20px; }
  .check-list li::before {
    content: ""; position: absolute; left: 0; top: 4px; width: 11px; height: 10px;
    background: var(--white); border-radius: 6px 6px 6px 1px;
  }
  .services-copy { position: absolute; top: 417px; width: 351px; }
  .service { margin: 0 0 18px; }
  .service__name {
    position: relative; margin: 0; padding-left: 19px;
    font-size: 16px; line-height: 20px; font-weight: 700; color: var(--green);
  }
  .service__name::before {
    content: ""; position: absolute; left: 0; top: 5px; width: 11px; height: 10px;
    background: var(--green); border-radius: 6px 6px 6px 1px;
  }
  .service__text { margin: 0 0 0 19px; }
</style>
</head>
<body>
<main class="brochure">
  <svg class="brochure__art" width="1200" height="848" viewBox="0 0 1200 848" aria-hidden="false">
    <defs>
      <linearGradient id="photoCaregiver" x1="0" y1="0" x2="1" y2="1">
        <stop offset="0" stop-color="var(--photo-warm-1)"/>
        <stop offset="1" stop-color="var(--photo-warm-2)"/>
      </linearGradient>
      <linearGradient id="photoNurse" x1="0" y1="0" x2="1" y2="1">
        <stop offset="0" stop-color="var(--photo-soft-1)"/>
        <stop offset="1" stop-color="var(--photo-soft-2)"/>
      </linearGradient>
      <linearGradient id="photoReading" x1="0" y1="0" x2="1" y2="1">
        <stop offset="0" stop-color="var(--photo-rose-1)"/>
        <stop offset="1" stop-color="var(--photo-rose-2)"/>
      </linearGradient>
    </defs>
    <rect x="0" y="0" width="400" height="340" fill="url(#photoCaregiver)" role="img" aria-label="Photo of a young caregiver smiling with an elderly woman at home"/>
    <rect x="400" y="0" width="400" height="320" fill="url(#photoNurse)" role="img" aria-label="Photo of a nurse with a stethoscope talking with a senior client"/>
    <rect x="800" y="0" width="400" height="380" fill="url(#photoReading)" role="img" aria-label="Photo of a caregiver reading a book with an elderly woman"/>

    <path class="panel-bg-left" d="M0,250 C80,285 200,330 330,330 C500,330 650,290 800,232 L800,848 L0,848 Z" fill="var(--white)"/>
    <path class="panel-bg-middle" d="M400,295 C580,280 720,245 800,228 L800,848 L400,848 Z" fill="var(--green)"/>
    <path class="wave-salmon" d="M0,205 C150,275 280,300 420,288 C580,272 720,240 800,222 L800,232 C650,290 500,330 330,330 C200,330 80,285 0,250 Z" fill="var(--salmon)"/>

    <path class="panel-bg-right" d="M800,255 C860,250 920,280 1000,320 C1080,360 1150,375 1200,372 L1200,848 L800,848 Z" fill="var(--white)"/>
    <path class="wave-green" d="M800,228 C860,195 950,210 1050,300 C1110,350 1160,365 1200,358 L1200,372 C1150,375 1080,360 1000,320 C920,280 860,250 800,255 Z" fill="var(--green)"/>
  </svg>

  <section class="panel panel--about">
    <h2 class="section-title">ABOUT</h2>
    <div class="about-copy">
      <p class="body-copy">Brantley Homecare is a state-licensed private duty home health care agency serving the island community of Oahu since 1996.</p>
      <p class="body-copy">We provide in-home services ranging from light housekeeping to personal care and skilled nursing.</p>
      <p class="body-copy">We strive to give compassionate, dependable care of the highest quality while maintaining extremely competitive rates. Everything we do is geared toward meeting the individual needs of our clients.</p>
      <p class="body-copy">Whether you need a little help or a lot of help, you’ll find that Brantley Homecare’s services are a cut above the rest.</p>
      <p class="body-copy">The Brantley Way is special; it is compassionate, professional, dependable, and flexible.</p>
    </div>
  </section>

  <section class="panel panel--team">
    <div class="team-block team-block--pros">
      <h3 class="team-heading">All of our Care Professionals:</h3>
      <ul class="check-list">
        <li>Are bonded, insured, and supervised;</li>
        <li>Have passed both criminal and abuse background checks;</li>
        <li>Have been screened for TB;</li>
        <li>Are certified in CPR and First Aid</li>
      </ul>
    </div>
    <div class="team-block team-block--nurse">
      <h3 class="team-heading">All client care is supervised by a licensed Nurse Care Consultant whose duties include:</h3>
      <ul class="check-list">
        <li>Regular home visits</li>
        <li>Client evaluation</li>
        <li>Care Professional supervision</li>
        <li>Revising/updating client care plans</li>
        <li>24/7 phone support</li>
      </ul>
    </div>
  </section>

  <section class="panel panel--services">
    <h2 class="section-title">SERVICES</h2>
    <div class="services-copy">
      <p class="body-copy">Brantley Homecare provides two different levels of care. Our Nurse Care Consultant will assist the client and family in determining the appropriate level of care needed during the complimentary initial consultation.</p>
      <div class="service">
        <h3 class="service__name">Nurse Aide Care</h3>
        <p class="body-copy service__text">Our Nurse Aides help you with your personal care needs, provide companionship, run errands, and do light housekeeping, along with assisting you with the activities of daily living.</p>
      </div>
      <div class="service">
        <h3 class="service__name">Skilled Nursing Care</h3>
        <p class="body-copy service__text">We offer a wide range of skilled nursing services using RN’s and LPN’s who provide treatment from wound care to life support, in addition to all of the services performed by our Nurse Aides.</p>
      </div>
    </div>
  </section>
</main>
</body>
</html>
```